Industrial Bolting Tool Safety Ad

We need an ad designed. Ad size is 4" x 4.75". Our company is VornelTek. We build large industrial bolting tools that are designed for use with very large bolts in large wind turbines (wind towers). If these large tools aren't equipped with some sort of safety measures, significant hand and wrist injuries can occur, such as crushed and mutilated fingers and hands. What makes our tools unique is that they are dual-levered (two handled), which means they require two hands to start, making accidental start highly unlikely. Safety is the thing we want to stress. Our tools help protect the most valuable asset - the tool operator. An image of a worker with a finger injury is attached to use for the background<br/>- VornelTek QX Company logo should be used (attached)<br/>- Ad headline should be: Safety is Vital in Critical Bolting<br/>- Ad subhead should be: <br/>High Torque Dual-Lever DC Nutrunners<br/>Designed with Safety in Mind<br/><br/>Apart from the safety aspect, here are some additional things to know. Our tool operates with a controller (a picture of the basic controller/tool setup is included with the design images). There is constant communication happening between the controller and the tool so that the bolts are tightened accurately every time. The controller works with many tools. An image of each model of tool is attached. Please include each image in the ad, although only one needs to be connected to the controller (the original image of the controller already has this so the other models can just stand free as-is).

Target Market(s)

Wind Turbine Manufacturers and Turbine Maintenance Engineers

Font styles to use
Sans Serif

Colors
9bcb3c
add136
cadf82

Requirements
Must have
• VornelTek QX Company Logo
• Headline: Safety is Vital in Critical Bolting
• Subhead: High-Torque Dual-Lever Nutrunners
• Designed with Safety in Mind

```html
<!DOCTYPE html>
<html lang="en">
<head>
<meta charset="utf-8">
<title>VornelTek QX – Safety Is Vital in Critical Bolting</title>
<link rel="stylesheet" href="https://fonts.googleapis.com/css2?family=Anton&family=Montserrat:wght@400;600;700&family=Titillium+Web:ital,wght@0,700;1,700&display=swap">
<style>
  :root {
    --stage: #a6a6a6;
    --ink: #231f20;
    --yellow: #f2c500;
    --white: #ffffff;
    --sky: #6f9bc8;
    --sky-light: #9fbbd6;
    --helmet: #1f9a55;
    --skin: #d59a80;
    --wound: #c8323e;
    --vest: #f0601e;
    --product: #c9c9c9;
  }
  html, body {
    margin: 0;
    width: 1200px;
    height: 1200px;
    overflow: hidden;
    background: var(--stage);
  }
  .ad {
    position: absolute;
    left: 120px;
    top: 30px;
    width: 960px;
    height: 1140px;
    box-shadow: 0 2px 6px rgba(0,0,0,.3);
  }
  .ad svg { display: block; width: 100%; height: 100%; }
  .headline {
    font-family: "Anton", "Oswald", sans-serif;
    fill: var(--white);
    stroke: var(--ink);
    stroke-width: 4;
    paint-order: stroke;
    text-anchor: middle;
  }
  .subhead {
    font-family: "Montserrat", sans-serif;
    font-weight: 600;
    font-size: 35px;
    fill: var(--white);
    text-anchor: middle;
  }
  .tagline {
    font-family: "Titillium Web", sans-serif;
    font-weight: 700;
    font-size: 24px;
    fill: var(--ink);
    text-anchor: middle;
  }
  .model-label {
    font-family: "Titillium Web", sans-serif;
    font-style: italic;
    font-weight: 700;
    font-size: 19px;
    fill: var(--white);
  }
  .body-copy {
    font-family: "Montserrat", sans-serif;
    font-size: 17px;
    fill: var(--white);
  }
  .call-label {
    font-family: "Montserrat", sans-serif;
    font-weight: 700;
    font-size: 24px;
    fill: var(--ink);
  }
  .call-number {
    font-family: "Montserrat", sans-serif;
    font-weight: 700;
    font-size: 36px;
    fill: #000;
  }
  .web-address {
    font-family: "Montserrat", sans-serif;
    font-weight: 600;
    font-size: 29px;
    letter-spacing: 2px;
    fill: var(--white);
    text-anchor: middle;
  }
  .brand-name {
    font-family: "Montserrat", sans-serif;
    font-weight: 700;
    font-size: 30px;
    fill: var(--white);
  }
  .brand-note {
    font-family: "Montserrat", sans-serif;
    font-size: 9px;
    fill: var(--white);
  }
</style>
</head>
<body>
<div class="ad">
  <svg viewBox="0 0 990 1176" xmlns="http://www.w3.org/2000/svg">
    <defs>
      <linearGradient id="photoTone" x1="0" y1="0" x2="0.9" y2="1">
        <stop offset="0" stop-color="var(--sky)"/>
        <stop offset="0.3" stop-color="var(--sky-light)"/>
        <stop offset="0.5" stop-color="#c9a899"/>
        <stop offset="0.68" stop-color="var(--skin)"/>
        <stop offset="0.82" stop-color="#cf6f55"/>
        <stop offset="1" stop-color="var(--vest)"/>
      </linearGradient>
    </defs>

    <rect class="photo" x="0" y="0" width="990" height="660" fill="url(#photoTone)" role="img" aria-label="Photo of a wind turbine worker in a green hard hat and orange vest pressing a bloodied cloth to an injured finger"/>

    <path class="swoosh-white" d="M0,588 Q420,662 990,358 L990,395 Q440,676 0,594 Z" fill="var(--white)"/>
    <path class="panel" d="M0,594 Q440,676 990,395 L990,1176 L0,1176 Z" fill="var(--ink)"/>
    <path class="swoosh-yellow" d="M330,626 Q660,640 990,400 L990,422 Q660,646 330,626 Z" fill="var(--yellow)"/>

    <text class="headline" x="495" y="133" font-size="95" textLength="730" lengthAdjust="spacingAndGlyphs">SAFETY IS VITAL IN</text>
    <text class="headline" x="495" y="255" font-size="115" textLength="858" lengthAdjust="spacingAndGlyphs">CRITICAL BOLTING</text>

    <text class="subhead" x="495" y="679" textLength="830" lengthAdjust="spacingAndGlyphs">HIGH TORQUE DUAL-LEVER DC NUTRUNNERS</text>

    <rect class="tagline-pill" x="120" y="700" width="753" height="50" rx="25" fill="var(--yellow)"/>
    <text class="tagline" x="496" y="734" textLength="724" lengthAdjust="spacingAndGlyphs">PROTECT YOUR MOST VALUABLE ASSET - THE TOOL OPERATOR</text>

    <g class="model-list">
      <circle cx="97" cy="812" r="41" fill="var(--product)" stroke="var(--yellow)" stroke-width="5" role="img" aria-label="17,000 Nm dual-lever tool"/>
      <text class="model-label" x="160" y="819">17,000 Nm Tool</text>
      <circle cx="97" cy="911" r="41" fill="var(--product)" stroke="var(--yellow)" stroke-width="5" role="img" aria-label="QP handle tool"/>
      <text class="model-label" x="162" y="918">QP Handle</text>
      <circle cx="97" cy="1014" r="41" fill="var(--product)" stroke="var(--yellow)" stroke-width="5" role="img" aria-label="QS handle tool"/>
      <text class="model-label" x="160" y="1021">QS Handle</text>
    </g>

    <line class="divider" x1="328" y1="788" x2="328" y2="1034" stroke="var(--white)" stroke-width="1.5"/>

    <circle class="system-shot" cx="470" cy="911" r="98" fill="var(--product)" stroke="var(--yellow)" stroke-width="7" role="img" aria-label="Controller in a rugged case connected to a dual-lever nutrunner"/>

    <g class="body-copy">
      <text x="600" y="853" textLength="326" lengthAdjust="spacingAndGlyphs">Specifically designed with operator</text>
      <text x="600" y="878" textLength="326" lengthAdjust="spacingAndGlyphs">safety in mind, VornelTek’s VTC4</text>
      <text x="600" y="903" textLength="326" lengthAdjust="spacingAndGlyphs">Gen IV Controller / QX Dual- Lever</text>
      <text x="600" y="928" textLength="326" lengthAdjust="spacingAndGlyphs">Nutrunner system provides an</text>
      <text x="600" y="953" textLength="326" lengthAdjust="spacingAndGlyphs">intuitive, intelligent solution even in</text>
      <text x="600" y="978">the harshest conditions.</text>
    </g>

    <g class="brand">
      <circle cx="72" cy="1100" r="14" fill="var(--white)"/>
      <text class="brand-name" x="96" y="1111">VornelTek QX</text>
      <text class="brand-note" x="150" y="1128">A Division of Halvern</text>
    </g>

    <g class="call">
      <rect x="465" y="1053" width="476" height="50" rx="25" fill="var(--white)"/>
      <path d="M490,1053 H615 V1103 H490 A25,25 0 0 1 490,1053 Z" fill="var(--yellow)"/>
      <text class="call-label" x="483" y="1086">CALL US:</text>
      <text class="call-number" x="618" y="1091" textLength="302" lengthAdjust="spacingAndGlyphs">1-800-555-0147</text>
    </g>

    <text class="web-address" x="703" y="1140" textLength="417" lengthAdjust="spacingAndGlyphs">www.halvern-global.com</text>
  </svg>
</div>
</body>
</html>
```